A private security company called "Tavron Security Services Ltd"

Hello everybody,

We need a web page for a company based in NZ. It is mainly an informative website so it would be wonderful if the designer puts their absolute best into making it a website that I would really appreciate. The website needs to show professionalism and also needs to make our web surfers find the information they need in a click. the company's colour is black and silver, and if those two colours could be integrated into the website it would be absolutely lovely. Please do contact me for any information.

Sincerely,
Dorian Vaskel

Industry/Entity Type

Security

```html
<!DOCTYPE html>
<html lang="en">
<head>
<meta charset="utf-8">
<title>Tavron Security Services Ltd</title>
<link href="https://fonts.googleapis.com/css2?family=PT+Sans+Narrow:wght@400;700&family=Arimo:wght@400;700&display=swap" rel="stylesheet">
<style>
:root{
  --ink:#1d1d1d;
  --text:#333333;
  --muted:#8a8a8a;
  --line:#cfcfcf;
  --footer-top:#4d4d4d;
  --footer-bottom:#1f1f1f;
  --footer-text:#9a9a9a;
  --white:#ffffff;
}
*{margin:0;padding:0;box-sizing:border-box}
html,body{width:1200px;height:2748px;overflow:hidden}
body{position:relative;background:var(--white);font-family:"Arimo",Arial,sans-serif;color:var(--text)}
.abs{position:absolute}
.heading{font-family:"PT Sans Narrow","Arial Narrow",sans-serif;color:var(--ink);font-weight:400}

/* header */
.site-header{left:0;top:0;width:1200px;height:157px;background:linear-gradient(#f7f7f7,#e6e6e6);border-bottom:1px solid #d5d5d5}
.brand{left:157px;top:62px;display:flex;align-items:center;gap:10px;font-family:"Arimo",Arial,sans-serif;font-weight:700;font-size:15px;color:var(--ink)}
.brand-dot{width:22px;height:22px;border-radius:50%;background:var(--ink)}
.tagline{left:418px;top:24px;font-family:"PT Sans Narrow","Arial Narrow",sans-serif;font-size:27px;color:var(--ink)}
.social{display:flex;gap:10px}
.social span{width:30px;height:30px;border-radius:50%;background:#b5b5b5;display:block}
.header-social{left:935px;top:31px}
.main-nav{left:418px;top:101px;display:flex;font-size:12px;color:var(--text)}
.main-nav a{color:inherit;text-decoration:none;margin-right:27px}
.main-nav a:last-child{margin-right:0}

/* hero */
.hero{left:0;top:157px;width:1200px;height:521px;background:linear-gradient(100deg,#4a4a4a 0%,#a9a9a9 30%,#d6d6d6 48%,#8c8c8c 62%,#2b2b2b 80%,#5a5a5a 100%)}
.hero-caption{left:0;top:337px;width:1200px;text-align:center;font-family:"PT Sans Narrow",sans-serif;font-size:31px;line-height:45px;color:#eeeeee;text-shadow:0 2px 4px rgba(0,0,0,.7)}
.hero-caption b{color:var(--white);font-weight:400}
.hero-arrow{top:398px;width:30px;height:34px}

/* solutions */
.solutions{left:0;top:678px;width:1200px;height:711px;background:linear-gradient(#f3f3f3,#dadada)}
.section-title{width:1200px;left:0;text-align:center;font-size:42px}
.services-title{left:157px;top:830px;font-size:26px}
.services-list{left:157px;top:888px;width:212px;list-style:none;font-size:12.5px;color:#666}
.services-list li{position:absolute;left:0;padding-left:32px;width:212px;line-height:17px}
.services-list li::before{content:"";position:absolute;left:2px;top:-2px;width:18px;height:18px;border-radius:50%;background:linear-gradient(#fafafa,#dcdcdc);border:1px solid #cfcfcf}
.services-list li::after{content:"";position:absolute;left:9px;top:4px;width:4px;height:4px;border-right:1.5px solid #888;border-top:1.5px solid #888;transform:rotate(45deg)}
.custom-box{left:157px;top:1100px;width:212px;height:251px;background:linear-gradient(#e8e8e8,#9f9f9f);border:1px solid #bdbdbd;text-align:center}
.custom-box .heading{margin-top:26px;font-size:24px;line-height:33px;color:#444;text-transform:uppercase}
.custom-box .brand-text{margin-top:70px;font-size:13px;font-weight:700;color:var(--ink)}
.col-line{width:1px;top:825px;height:560px;background:var(--line)}
.row-line{height:1px;background:var(--line)}
.card{width:196px}
.card-photo{width:196px;height:104px;border:4px solid var(--white);box-shadow:0 1px 3px rgba(0,0,0,.25)}
.card-title{font-size:20px;margin-top:12px}
.card-text{font-size:11px;line-height:15px;color:#777;margin-top:8px}
.btn{display:inline-block;background:linear-gradient(#ffffff,#dedede);border:1px solid #b9b9b9;border-radius:3px;color:var(--text);font-size:11.5px;height:28px;line-height:26px;padding:0 13px}
.card .btn{position:absolute;right:0}

/* industries */
.industries{left:0;top:1389px;width:1200px;height:402px;background:var(--white)}
.ind-item{top:1534px;width:196px;text-align:center}
.ind-photo{width:196px;height:157px;border:4px solid #ececec;box-shadow:0 0 2px rgba(0,0,0,.25)}
.ind-label{margin-top:20px;font-family:"PT Sans Narrow",sans-serif;font-size:17px;color:var(--ink)}
.round-arrow{width:34px;height:34px}

/* residential / commercial */
.solutions-split{left:0;top:1791px;width:1200px;height:483px;background:linear-gradient(#f6f6f6,#ececec)}
.split-divider{left:602px;top:1830px;width:2px;height:400px;background:linear-gradient(rgba(200,200,200,0),#d0d0d0,rgba(200,200,200,0))}
.split-item{top:1864px;width:420px;text-align:center}
.round-photo{width:184px;height:184px;margin:0 auto;border-radius:50%;border:7px solid #e6e6e6;box-shadow:0 2px 6px rgba(0,0,0,.2)}
.split-item .heading{font-size:21px;margin-top:22px}
.split-item p{font-size:12px;line-height:15px;color:#8a8a8a;margin:10px auto 0;width:360px}
.split-item .btn{margin-top:26px;padding:0 22px;height:32px;line-height:30px;font-size:13px}

/* footer */
.site-footer{left:0;top:2274px;width:1200px;height:474px;background:radial-gradient(ellipse at 40% 0%,#5a5a5a 0%,var(--footer-top) 35%,var(--footer-bottom) 100%)}
.footer-title{top:2330px;font-size:30px;color:var(--white)}
.footer-about{left:157px;top:2398px;width:305px;font-size:11.5px;line-height:14px;color:var(--footer-text)}
.footer-about p+p{margin-top:14px}
.quick-links{left:540px;top:2400px;list-style:none;font-size:11.5px;color:var(--footer-text);width:130px}
.quick-links li{position:absolute;left:0;padding-left:22px;width:130px;line-height:14px}
.quick-links li::before{content:"";position:absolute;left:2px;top:3px;width:5px;height:5px;border-right:1.5px solid #ddd;border-top:1.5px solid #ddd;transform:rotate(45deg)}
.contact-company{left:770px;top:2400px;font-size:11.5px;font-weight:700;color:#b5b5b5;letter-spacing:.5px;text-transform:uppercase}
.contact-line{left:770px;font-size:11.5px;line-height:14px;color:var(--footer-text);display:flex;gap:12px}
.contact-line svg{flex:none}
.footer-rule{left:157px;top:2660px;width:888px;height:1px;background:#141414;box-shadow:0 1px 0 #444}
.copyright{left:157px;top:2700px;font-size:11.5px;color:#aaa}
.footer-social{left:932px;top:2690px}
.footer-social span{background:#8a8a8a}
</style>
</head>
<body>

<header class="abs site-header">
  <div class="abs brand"><span class="brand-dot"></span>Tavron Security Services Ltd</div>
  <div class="abs tagline">Vigilance You Can Rely On</div>
  <div class="abs social header-social"><span></span><span></span><span></span></div>
  <nav class="abs main-nav">
    <a href="#">HOME</a><a href="#">ABOUT US</a><a href="#">OUR SECURITY SOLUTIONS</a><a href="#">INDUSTRIES WE SERVE</a><a href="#">CONTACT US</a>
  </nav>
</header>

<section class="abs hero" role="img" aria-label="Black and white photo of a uniformed security guard looking out over city skyscrapers"></section>
<div class="abs hero-caption"><b>Personal BodyGuards</b> is simply dummy text of<br>the printing and typesetting industry.</div>
<svg class="abs hero-arrow" style="left:118px" viewBox="0 0 30 34"><path d="M19 6 L9 17 L19 28" fill="none" stroke="#ffffff" stroke-width="2"/></svg>
<svg class="abs hero-arrow" style="left:1052px" viewBox="0 0 30 34"><path d="M11 6 L21 17 L11 28" fill="none" stroke="#ffffff" stroke-width="2"/></svg>

<section class="abs solutions"></section>
<h2 class="abs heading section-title" style="top:726px">Our Security Solutions</h2>

<h3 class="abs heading services-title">Services</h3>
<ul class="abs services-list">
  <li style="top:0">Property guards</li>
  <li style="top:36px">Corporate events security</li>
  <li style="top:73px">Personal bodyguard for high net worth individuals</li>
  <li style="top:124px">Security consultancy</li>
  <li style="top:160px">Private investigation</li>
</ul>
<div class="abs custom-box">
  <div class="heading">Custom Options<br>Available</div>
  <div class="brand-text">Tavron Security Services Ltd</div>
</div>

<div class="abs col-line" style="left:377px"></div>
<div class="abs col-line" style="left:599px"></div>
<div class="abs col-line" style="left:821px"></div>
<div class="abs col-line" style="left:1044px"></div>
<div class="abs row-line" style="left:377px;top:1086px;width:222px"></div>
<div class="abs row-line" style="left:599px;top:1094px;width:222px"></div>
<div class="abs row-line" style="left:821px;top:1057px;width:223px"></div>

<article class="abs card" style="left:392px;top:826px">
  <div class="card-photo" role="img" aria-label="Photo of a model house held in hands" style="background:linear-gradient(#d8d2c8,#8b6a4d)"></div>
  <h4 class="heading card-title">Property Guards</h4>
  <p class="card-text">Trained guards patrol and secure your homes, sites and assets day and night.</p>
  <span class="btn" style="top:203px">Read More</span>
</article>
<article class="abs card" style="left:392px;top:1094px">
  <div class="card-photo" role="img" aria-label="Photo of event security staff in black jackets" style="background:linear-gradient(#9aa4ad,#1f2530)"></div>
  <h4 class="heading card-title">Corporate Events Security</h4>
  <p class="card-text">Uniformed teams manage access, crowds and safety at your corporate events.</p>
  <span class="btn" style="top:212px">Read More</span>
</article>
<article class="abs card" style="left:614px;top:826px">
  <div class="card-photo" role="img" aria-label="Photo of a bodyguard in a dark suit" style="background:linear-gradient(#6b7580,#141820)"></div>
  <h4 class="heading card-title">Personal Bodyguards</h4>
  <p class="card-text">Discreet close protection officers keep you safe at home, at work and travelling.</p>
  <span class="btn" style="top:222px">Read More</span>
</article>
<article class="abs card" style="left:614px;top:1108px">
  <div class="card-photo" role="img" aria-label="Photo of consultants meeting at a table" style="background:linear-gradient(#d9d9d9,#5d5d5d)"></div>
  <h4 class="heading card-title">Security Consultancy</h4>
  <p class="card-text">Expert reviews of your risks, plans and systems with practical advice for your team.</p>
  <span class="btn" style="top:216px">Read More</span>
</article>
<article class="abs card" style="left:836px;top:826px">
  <div class="card-photo" role="img" aria-label="Photo of an investigator with a camera in a car" style="background:linear-gradient(#c7d3dd,#3a3f45)"></div>
  <h4 class="heading card-title">Private Investigation</h4>
  <p class="card-text">Licensed investigators gather facts quietly and report clearly to you.</p>
  <span class="btn" style="top:188px">Read More</span>
</article>
<article class="abs card" style="left:836px;top:1072px">
  <div class="card-photo" role="img" aria-label="Photo of protection officers beside a black car" style="background:linear-gradient(#a9a9a9,#1b1b1b)"></div>
  <h4 class="heading card-title">Executive Protection</h4>
  <p class="card-text">Senior protection staff escort executives with planned routes, vehicles and close cover at all times.</p>
  <span class="btn" style="top:240px">Read More</span>
</article>

<section class="abs industries"></section>
<h2 class="abs heading section-title" style="top:1432px">Industries We Serve</h2>
<svg class="abs round-arrow" style="left:108px;top:1594px" viewBox="0 0 34 34"><circle cx="17" cy="17" r="16" fill="#bdbdbd"/><path d="M19 11 L13 17 L19 23" fill="none" stroke="#fff" stroke-width="2"/></svg>
<svg class="abs round-arrow" style="left:1058px;top:1594px" viewBox="0 0 34 34"><circle cx="17" cy="17" r="16" fill="#bdbdbd"/><path d="M15 11 L21 17 L15 23" fill="none" stroke="#fff" stroke-width="2"/></svg>
<div class="abs ind-item" style="left:157px">
  <div class="ind-photo" role="img" aria-label="Photo of a hand holding a glowing circuit card" style="background:radial-gradient(circle at 55% 50%,#3fb3e6,#0b3f78 75%)"></div>
  <div class="ind-label">Technology &amp; Communication</div>
</div>
<div class="abs ind-item" style="left:388px">
  <div class="ind-photo" role="img" aria-label="Photo of a construction worker in a hard hat" style="background:linear-gradient(#c8d6e3,#a9896a 60%,#6a5744)"></div>
  <div class="ind-label">Energy &amp; Construction</div>
</div>
<div class="abs ind-item" style="left:620px">
  <div class="ind-photo" role="img" aria-label="Photo of a bright hospital ward" style="background:linear-gradient(#eaf4fb,#8fc0e0)"></div>
  <div class="ind-label">Healthcare</div>
</div>
<div class="abs ind-item" style="left:850px">
  <div class="ind-photo" role="img" aria-label="Photo of a laboratory worker with safety glasses" style="background:linear-gradient(#f1f1ee,#b9bfb4)"></div>
  <div class="ind-label">Transportation &amp; Logistics</div>
</div>

<section class="abs solutions-split"></section>
<div class="abs split-divider"></div>
<div class="abs split-item" style="left:120px">
  <div class="round-photo" role="img" aria-label="Photo of a woman at the front door of her home" style="background:linear-gradient(#cdbba3,#8a6b52)"></div>
  <h3 class="heading">Residential Solutions</h3>
  <p>Alarm monitoring, patrols and rapid response for homes across the region, with friendly local staff who know your street and check in on every visit.</p>
  <span class="btn">Read More</span>
</div>
<div class="abs split-item" style="left:660px">
  <div class="round-photo" role="img" aria-label="Photo of a security guard standing before city towers" style="background:linear-gradient(#8fb6da,#2c3c4e)"></div>
  <h3 class="heading">Commercial Solutions</h3>
  <p>Guarding, access control and monitoring for offices, retail and industrial sites, shaped around your hours, your people and the risks you face every day.</p>
  <span class="btn">Read More</span>
</div>

<footer class="abs site-footer"></footer>
<h3 class="abs heading footer-title" style="left:157px">About us</h3>
<div class="abs footer-about">
  <p>Tavron Security Services Ltd has protected people, property and businesses across New Zealand for many years. Our licensed officers are trained, vetted and ready to respond, and every contract is built around the needs of the client.</p>
  <p>We combine guarding, close protection, investigation and consultancy under one roof, so clients deal with one trusted team. Call us any time to discuss your site, your event or your family's safety and we will plan with you.</p>
</div>
<h3 class="abs heading footer-title" style="left:540px">Quick Links</h3>
<ul class="abs quick-links">
  <li style="top:0">HOME</li>
  <li style="top:32px">ABOUT US</li>
  <li style="top:64px">OUR SECURITY SOLUTIONS</li>
  <li style="top:112px">INDUSTRIES WE SERVE</li>
  <li style="top:164px">CONTACT US</li>
</ul>
<h3 class="abs heading footer-title" style="left:768px">Contact Us</h3>
<div class="abs contact-company">Tavron Security Services Ltd.</div>
<div class="abs contact-line" style="top:2444px">
  <svg width="14" height="18" viewBox="0 0 14 18"><path d="M7 0a6 6 0 0 1 6 6c0 4.5-6 12-6 12S1 10.5 1 6a6 6 0 0 1 6-6z" fill="#e6e6e6"/><circle cx="7" cy="6" r="2.3" fill="#333"/></svg>
  <span>12 Harbour View Rd, Takapuna,<br>Auckland 0622, New Zealand</span>
</div>
<div class="abs contact-line" style="top:2484px">
  <svg width="14" height="16" viewBox="0 0 14 16"><path d="M3 1l3 3-2 2c1 2 2.5 3.5 4.5 4.5l2-2 3 3-2 3C6 14 1 8 1 3z" fill="#e6e6e6"/></svg>
  <span>+64 9 555 0142</span>
</div>
<div class="abs contact-line" style="top:2518px">
  <svg width="16" height="12" viewBox="0 0 16 12"><rect width="16" height="12" rx="1" fill="#e6e6e6"/><path d="M1 1l7 6 7-6" fill="none" stroke="#333" stroke-width="1.3"/></svg>
  <span>info@tavronsecurity.co.nz</span>
</div>
<div class="abs footer-rule"></div>
<div class="abs copyright">Copyright © 2014 Tavron Security Service LTD.</div>
<div class="abs social footer-social"><span></span><span></span><span></span></div>

</body>
</html>
```